Residential Remodeling Contractor needs updated business card

I need a new design for my business card.
Name of the company is Ridgefell Construction. I need a card that commands presence, strength, integrity. I have been in business for 28 years. I am a Residential Remodeling Contractor that covers all aspects of a residential remodel and build.

```html
<!DOCTYPE html>
<html lang="en">
<head>
<meta charset="utf-8">
<title>Ridgefell Construction — Business Card</title>
<link href="https://fonts.googleapis.com/css2?family=Cinzel:wght@600;700&family=Arimo:wght@400&display=swap" rel="stylesheet">
<style>
  :root {
    --navy: #1b3f7d;
    --white: #ffffff;
    --backdrop: #3a3a3c;
    --rule: rgba(255,255,255,0.7);
  }
  * { box-sizing: border-box; margin: 0; padding: 0; }
  html, body { width: 1200px; height: 901px; overflow: hidden; }
  body {
    background: var(--backdrop);
    position: relative;
    font-family: "Arimo", Arial, sans-serif;
  }
  .card {
    position: absolute;
    top: 296px;
    width: 540px;
    height: 309px;
    border-radius: 18px;
    background: var(--navy);
    overflow: hidden;
    color: var(--white);
    box-shadow: 0 10px 24px rgba(0,0,0,0.45);
  }
  .card--front { left: 40px; }
  .card--back { left: 620px; }

  .wordmark {
    font-family: "Cinzel", "Times New Roman", serif;
    font-weight: 700;
    color: var(--white);
    line-height: 1;
    letter-spacing: 0.02em;
  }
  .wordmark span { display: block; }

  .card--front .wordmark {
    position: absolute;
    left: 0; right: 0;
    top: 110px;
    text-align: center;
  }
  .card--front .wordmark__line1 { font-size: 44px; }
  .card--front .wordmark__line2 { font-size: 34px; margin-top: 6px; padding-left: 40px; }

  .back__panel {
    position: absolute;
    top: 0; right: 0;
    width: 150px; height: 100%;
    background: var(--white);
  }

  .card--back .wordmark {
    position: absolute;
    left: 40px;
    top: 36px;
  }
  .card--back .wordmark__line1 { font-size: 30px; }
  .card--back .wordmark__line2 { font-size: 23px; margin-top: 4px; padding-left: 24px; }

  .person {
    position: absolute;
    left: 40px;
    top: 132px;
  }
  .person__name {
    font-family: "Cinzel", "Times New Roman", serif;
    font-weight: 700;
    font-size: 22px;
    letter-spacing: 0.02em;
  }
  .person__title {
    font-size: 13px;
    margin-top: 4px;
  }
  .person__rule {
    width: 16px;
    height: 1px;
    background: var(--rule);
    margin: 10px 0 8px;
  }
  .contact { list-style: none; }
  .contact li {
    display: flex;
    align-items: center;
    gap: 7px;
    font-size: 12.5px;
    line-height: 19px;
  }
  .contact svg { width: 11px; height: 11px; fill: var(--white); flex: none; }
</style>
</head>
<body>

  <section class="card card--front" aria-label="Card front">
    <div class="wordmark">
      <span class="wordmark__line1">Ridgefell</span>
      <span class="wordmark__line2">Construction</span>
    </div>
  </section>

  <section class="card card--back" aria-label="Card back">
    <div class="back__panel"></div>

    <div class="wordmark">
      <span class="wordmark__line1">Ridgefell</span>
      <span class="wordmark__line2">Construction</span>
    </div>

    <div class="person">
      <p class="person__name">Daniel Whitcombe</p>
      <p class="person__title">Owner &amp; Manager</p>
      <div class="person__rule"></div>
      <ul class="contact">
        <li>
          <svg viewBox="0 0 12 12" aria-hidden="true"><path d="M1 4c0-2 2-3 5-3s5 1 5 3l-2 1-1-1.5H4L3 5zM2.5 6h7l1 5h-9z"/></svg>
          555 014 2288
        </li>
        <li>
          <svg viewBox="0 0 12 12" aria-hidden="true"><path d="M3 0h6v12H3zM4 1v9h4V1z"/></svg>
          555-013-47720
        </li>
        <li>
          <svg viewBox="0 0 12 12" aria-hidden="true"><path d="M0 2h12v8H0zM1 3l5 4 5-4v-0.2H1z"/></svg>
          info@ridgefellconstruction.com
        </li>
        <li>
          <svg viewBox="0 0 12 12" aria-hidden="true"><circle cx="6" cy="6" r="5.5"/><path d="M3 4c1 0 2 1 1.5 2S6 8 5 10M8 2c0 2 2 2 3 3" stroke="#1b3f7d" stroke-width="1" fill="none"/></svg>
          www.ridgefellconstruction.com
        </li>
      </ul>
    </div>
  </section>

</body>
</html>
```